Market Research firm needs updated business cards with new logo

We need the logo to be included somewhere on the card (attached). We would also like the phrases "Independent, Objective, Comprehensive" and "Research You Can Trust" somewhere on the card. Front or back. Our colors are hex codes 6075a7, e48d25 and 5a5b5b. Though you are certainly not limited to those shades, whatever you produce should coordinate with them. I have also attached our favicon. Feel free to use it in your design, but please do not use it to replace the full logo.

Contact Information for Business Card

see project description

Font styles to use
Other font styles liked:
• Open Sans

Requirements
Must have
• the logo
• We use Open Sans font

```html
<!DOCTYPE html>
<html lang="en">
<head>
<meta charset="utf-8">
<title>Veritas Insight – Business Cards</title>
<link rel="stylesheet" href="https://fonts.googleapis.com/css2?family=Open+Sans:wght@400;600;700&family=Roboto:wght@400;500&family=Tinos&display=swap">
<style>
  :root {
    --charcoal: #58595a;
    --orange: #e48d25;
    --slate-blue: #6075a7;
    --paper: #ffffff;
    --backdrop: #4f4d4b;
  }
  * { box-sizing: border-box; margin: 0; padding: 0; }
  html, body {
    width: 1200px; height: 960px; overflow: hidden;
    background: var(--backdrop);
  }
  .sheet { position: relative; width: 1200px; height: 960px; }
  .card {
    position: absolute; left: 250px; width: 700px; height: 400px;
    background: var(--paper); overflow: hidden;
    box-shadow: 0 10px 30px rgba(0,0,0,.35);
  }
  .card--back { top: 50px; }
  .card--front { top: 510px; }
  .card__swoosh { position: absolute; inset: 0; width: 100%; height: 100%; }
  .brand {
    position: absolute; display: flex; align-items: center; gap: 8px;
    font-family: "Open Sans", sans-serif; font-weight: 600;
    font-size: 30px; color: var(--slate-blue); letter-spacing: .2px;
  }
  .brand__dot { width: 14px; height: 14px; border-radius: 50%; background: var(--orange); }
  .card--back .brand { right: 60px; top: 90px; }
  .card--front .brand { right: 50px; top: 36px; }
  .tagline {
    position: absolute; left: 70px; top: 170px; width: 230px;
    font-family: "Tinos", serif; font-size: 16px; line-height: 1.25;
    color: var(--paper); text-align: center;
  }
  .person { position: absolute; left: 0; top: 118px; display: flex; align-items: flex-start; }
  .person__bar { width: 72px; height: 22px; background: var(--orange); margin-top: 14px; }
  .person__text { margin-left: 12px; color: var(--paper); font-family: "Open Sans", sans-serif; }
  .person__name { font-size: 28px; font-weight: 700; line-height: 1.1; }
  .person__role { font-size: 18px; font-weight: 400; line-height: 1.1; }
  .contacts { position: absolute; left: 110px; top: 235px; list-style: none; }
  .contact { display: flex; align-items: center; gap: 18px; height: 52px; }
  .contact__icon {
    width: 38px; height: 38px; border-radius: 50%; background: var(--orange);
    display: flex; align-items: center; justify-content: center; flex: none;
  }
  .contact__text {
    font-family: "Roboto", sans-serif; font-size: 16px; line-height: 1.2; color: var(--paper);
  }
</style>
</head>
<body>
<main class="sheet">

  <section class="card card--back" aria-label="Card back">
    <svg class="card__swoosh" viewBox="0 0 700 400" preserveAspectRatio="none" aria-hidden="true">
      <path fill="var(--orange)" d="M0,0 H252 C380,0 440,140 492,240 C552,355 620,395 700,398 V400 H0 Z"/>
      <path fill="var(--charcoal)" d="M0,0 H232 C360,0 420,140 472,240 C532,355 600,395 680,400 H0 Z"/>
    </svg>
    <div class="brand"><span class="brand__dot"></span>Veritas Insight</div>
    <p class="tagline">Independent, Objective<br>Comprehensive and<br>Research You Can Trust</p>
  </section>

  <section class="card card--front" aria-label="Card front">
    <svg class="card__swoosh" viewBox="0 0 700 400" preserveAspectRatio="none" aria-hidden="true">
      <path fill="var(--orange)" d="M0,0 H252 C380,0 440,140 492,240 C552,355 620,395 700,398 V400 H0 Z"/>
      <path fill="var(--charcoal)" d="M0,0 H232 C360,0 420,140 472,240 C532,355 600,395 680,400 H0 Z"/>
    </svg>
    <div class="brand"><span class="brand__dot"></span>Veritas Insight</div>

    <div class="person">
      <span class="person__bar"></span>
      <div class="person__text">
        <p class="person__name">JHON DOE</p>
        <p class="person__role">FOUNDER</p>
      </div>
    </div>

    <ul class="contacts">
      <li class="contact">
        <span class="contact__icon">
          <svg width="18" height="18" viewBox="0 0 24 24" aria-hidden="true"><path fill="#fff" d="M6.6 10.8a15 15 0 0 0 6.6 6.6l2.2-2.2a1 1 0 0 1 1-.25 11.4 11.4 0 0 0 3.6.57 1 1 0 0 1 1 1V20a1 1 0 0 1-1 1A17 17 0 0 1 3 4a1 1 0 0 1 1-1h3.5a1 1 0 0 1 1 1c0 1.25.2 2.45.57 3.57a1 1 0 0 1-.25 1z"/></svg>
        </span>
        <p class="contact__text">+8801000123456<br>+8801000654321</p>
      </li>
      <li class="contact">
        <span class="contact__icon">
          <svg width="20" height="20" viewBox="0 0 24 24" aria-hidden="true" fill="none" stroke="#fff" stroke-width="1.8"><circle cx="12" cy="12" r="9"/><path d="M3 12h18M12 3c3 3 3 15 0 18M12 3c-3 3-3 15 0 18"/></svg>
        </span>
        <p class="contact__text">www.northfieldstudio.com<br>www.northfield.com</p>
      </li>
      <li class="contact">
        <span class="contact__icon">
          <svg width="18" height="18" viewBox="0 0 24 24" aria-hidden="true"><path fill="#fff" d="M12 2a7 7 0 0 0-7 7c0 5 7 13 7 13s7-8 7-13a7 7 0 0 0-7-7zm0 9.5A2.5 2.5 0 1 1 12 6.5a2.5 2.5 0 0 1 0 5z"/></svg>
        </span>
        <p class="contact__text">North Kamalpur,Rayerbag<br>Dhaka</p>
      </li>
    </ul>
  </section>

</main>
</body>
</html>
```